We need a modern WIX website for Brightform Beam Services Australia (Laser/Industrial/Engineering)

We need a website for Wix (coded) for our laser restoration and industrial cleaning business.

It will need to be 4-6 pages.
Pages may include:
Home
About
Why Laser
Capabilities
There needs to be a contact / quote form

We do not want boring institutional design, so please do try to be a little creative (but not artsy, more engineering / laser etc). We hesitate with boxy wordpress looking templates, so please bring in strip backgrounds and sliders etc;

Our brand colours are blue and red, but a sharp modern site relative to the industry and work is important.

We envision the home page to take visitors on a informed journey of who, what, why, how, explaining the capability of laser science across contaminants, industries and surfaces.

We envision the home page to be strips:
- landing
- intro

-Why choose laser / What is laser cleaning
Minimum downtime, no surface damage, no environmental impact, no mess, no waste, complete restoration (we have an explainer video)

- Contaminants
Bacteria, Rust, Corrosion, Oxides, Grease, Oil, Paint, Stains, Mold, Soot / Carbon, Graffiti, Coatings, Dirt, Residue

- Surfaces
Metals, Engines/Parts/Components, Tools, Machinery, Bricks/Blockwork, Concrete, Paint, Stone, Wood, Aluminium

- Industries
Medical/Sterile, Hospitality, Bio Hazardous, Construction, Infrastructure, Property, Industrial, Engineer, Automotive, Marine, Heritage, Non Destructive Testing,

----
Here is some info on the company below:

"Background Information - Brightform Beam Services Australia (BBSA) is a leading provider of advanced laser restoration services for the residential, commercial, medical, hazardous and industrial sectors, offering waste free, chemical free and damage free complete restoration of metals, concrete, wood, stone and heritage, hygiene and hazard surfaces, with complete removal of coatings, bacteria, paint, rust, graffiti, mold and fire ash (soot), and preparation and treating for welding and bonding.
Servicing Melbourne and Victoria, with additional services available Australia wide, BBSA offers a 24/7 call-out service to your site.
With no downtime to your operations, we offer a timely resolution to your cleaning and maintenance needs."

We have attached some inspiration of websites we like the flow/feel of, but feel free to put your best designs forward.

You are welcome to use dummy headers and text at this stage, as design and feel is most important, and we can add text later.

```html
<!DOCTYPE html>
<html lang="en">
<head>
<meta charset="utf-8">
<title>Brightform Beam Services Australia</title>
<link href="https://fonts.googleapis.com/css2?family=Michroma&family=Roboto:wght@400;500;700&display=swap" rel="stylesheet">
<style>
:root{
  --black:#000;
  --ink:#111;
  --white:#fff;
  --red:#e8161f;
  --blue:#1a72c0;
  --icon-blue:#1669b7;
  --muted:#cfcfcf;
  --panel:rgba(20,20,24,.82);
}
*{margin:0;padding:0;box-sizing:border-box}
html,body{width:1200px;height:3720px;overflow:hidden;background:var(--black)}
body{position:relative;font-family:'Roboto',sans-serif;color:var(--white)}
.abs{position:absolute}
.display{font-family:'Michroma',sans-serif;font-weight:400}

/* header */
.site-header{left:0;top:0;width:1200px;height:85px;background:var(--black)}
.brand{left:113px;top:18px;font-size:40px;font-weight:700;letter-spacing:2px;line-height:48px}
.nav{left:406px;top:33px;display:flex;gap:0;font-size:14px}
.nav a{color:var(--white);text-decoration:none;position:absolute;white-space:nowrap}
.call-btn{left:855px;top:25px;width:233px;height:40px;background:var(--red);border-radius:3px;font-size:13px;display:flex;align-items:center;justify-content:center;gap:7px}

/* hero */
.hero{left:0;top:85px;width:1200px;height:745px;
  background:radial-gradient(circle at 600px 330px,#f0a040 0,#b6621b 9%,rgba(60,70,110,.5) 30%,transparent 55%),
  linear-gradient(180deg,#2c3c66 0%,#1b2647 50%,#0b0f1c 85%,#000 100%)}
.hero-panel{left:89px;top:290px;width:427px;height:275px;background:var(--panel)}
.tag{left:22px;top:24px;width:192px;height:36px;background:var(--blue);font-family:'Michroma',sans-serif;font-size:14px;letter-spacing:4px;display:flex;align-items:center;justify-content:center}
.hero-title{left:22px;top:70px;font-size:50px;letter-spacing:2px}
.hero-text{left:22px;top:135px;width:390px;font-size:20px;line-height:26px}
.btn{background:var(--red);color:var(--white);font-size:13px;font-weight:700;display:flex;align-items:center;justify-content:center;border-radius:2px}
.hero-btn{left:22px;top:206px;width:132px;height:40px}
.slide-arrow{left:1125px;width:38px;height:38px;border-radius:50%;background:var(--white);display:flex;align-items:center;justify-content:center}

/* about */
.about-photo{left:120px;top:873px;width:420px;height:420px;background:linear-gradient(180deg,#8d9aa8 0%,#3b4656 45%,#1a2230 75%,#2c3442 100%)}
.frame-red{left:111px;top:862px;width:161px;height:178px;border-left:3px solid var(--red);border-top:3px solid var(--red)}
.frame-white{left:397px;top:1133px;width:161px;height:178px;border-right:5px solid var(--white);border-bottom:5px solid var(--white)}
.section-title{font-size:50px;letter-spacing:1px}
.about-title{left:612px;top:866px}
.about-copy{left:612px;top:944px;width:473px;font-size:13.5px;line-height:25.7px;text-align:justify}
.about-copy p+p{margin-top:25px}
.about-btn{left:612px;top:1279px;width:130px;height:40px}

/* why laser */
.why{left:0;top:1400px;width:1200px;height:600px;background:radial-gradient(ellipse at 600px 150px,#2a3040 0,#161a24 45%,#07080c 90%)}
.why-title{left:0;top:1548px;width:1200px;text-align:center}
.why-card{top:1661px;height:189px;background:var(--white);color:var(--ink);display:flex;flex-direction:column;align-items:center;justify-content:flex-start;padding-top:30px;font-size:16px;font-weight:500;text-align:center;line-height:26px}
.why-card svg{margin-bottom:6px}
.why-card.active{top:1635px;height:241px;background:var(--blue);color:var(--white);padding-top:40px}

/* video */
.video{left:111px;top:2057px;width:977px;height:483px;background:radial-gradient(circle at 488px 230px,#f5a040 0,#9a4a12 14%,#3a3d48 40%,#15171d 80%)}
.play{left:450px;top:203px;width:76px;height:76px;border-radius:50%;background:var(--red);display:flex;align-items:center;justify-content:center}

/* tabs */
.tabs{left:0;top:2658px;width:1200px;height:132px;background:var(--white);display:flex}
.tab{width:400px;display:flex;align-items:center;justify-content:center;color:var(--ink);font-size:29px;font-weight:500}
.tab.active{background:var(--red);color:var(--white);position:relative}
.tab.active::after{content:"";position:absolute;left:183px;top:132px;border-left:17px solid transparent;border-right:17px solid transparent;border-top:30px solid var(--red)}
.surface{width:140px;text-align:center;font-size:16px;font-weight:700}
.surface .disc{width:108px;height:108px;margin:0 auto 18px;border-radius:50%;background:#1d1d1d;display:flex;align-items:center;justify-content:center}

/* footer */
.site-footer{left:0;top:3320px;width:1200px;height:400px;background:linear-gradient(180deg,#000 0,#141820 45%,#262626 100%)}
.foot-col{top:3408px}
.foot-col h3{font-size:21px;font-weight:700;margin-bottom:10px}
.foot-col li{list-style:none;font-size:14px;line-height:25.6px;display:flex;align-items:center;gap:12px}
.social{display:flex;gap:7px}
.social span{width:33px;height:33px;background:var(--white);display:block}
.copyright{left:0;top:3622px;width:1200px;text-align:center;font-size:14px}
</style>
</head>
<body>

<header class="abs site-header">
  <div class="abs brand">BBSA</div>
  <nav class="abs nav" style="left:0;top:35px">
    <a style="left:406px">Home</a>
    <a style="left:481px">About</a>
    <a style="left:556px">Why Laser</a>
    <a style="left:660px">Capabilities</a>
    <a style="left:771px">Contact</a>
  </nav>
  <div class="abs call-btn">
    <svg width="13" height="13" viewBox="0 0 24 24"><path fill="#fff" d="M6.6 10.8a15 15 0 0 0 6.6 6.6l2.2-2.2c.3-.3.7-.4 1-.2 1.1.4 2.3.6 3.6.6.6 0 1 .4 1 1V20c0 .6-.4 1-1 1A17 17 0 0 1 3 4c0-.6.4-1 1-1h3.5c.6 0 1 .4 1 1 0 1.3.2 2.5.6 3.6.1.3 0 .7-.2 1z"/></svg>
    Call Us : <b>+61 3 9555 0142</b>
  </div>
</header>

<section class="abs hero" role="img" aria-label="Laser cutting head throwing bright orange sparks over a metal sheet"></section>
<div class="abs hero-panel">
  <div class="abs tag">WELCOME TO</div>
  <div class="abs hero-title display">BBSA</div>
  <p class="abs hero-text">We are a laser restoration and industrial cleaning business</p>
  <div class="abs btn hero-btn">GET STARTED</div>
</div>
<div class="abs slide-arrow" style="top:390px"><svg width="14" height="14" viewBox="0 0 14 14"><path d="M3 9l4-4 4 4" fill="none" stroke="#111" stroke-width="1.8"/></svg></div>
<div class="abs slide-arrow" style="top:441px"><svg width="14" height="14" viewBox="0 0 14 14"><path d="M3 5l4 4 4-4" fill="none" stroke="#111" stroke-width="1.8"/></svg></div>

<div class="abs frame-red"></div>
<div class="abs about-photo" role="img" aria-label="Close-up of an industrial laser machine head emitting a fine beam"></div>
<div class="abs frame-white"></div>
<h2 class="abs section-title display about-title">ABOUT US</h2>
<div class="abs about-copy">
  <p>Brightform Beam Services Australia (BBSA) is a leading provider of advanced laser restoration services for the residential, commercial, medical, hazardous and industrial sectors, offering waste free, chemical free and damage free complete restoration of metals, concrete, wood, stone and heritage, hygiene and hazard surfaces, with complete removal of coatings, bacteria, paint, rust, graffiti, mold and fire ash (soot), and preparation and treating for welding and bonding.</p>
  <p>Servicing Melbourne and Victoria, with additional services available Australia wide, BBSA offers a 24/7 call-out service to your site. With no downtime to your operations, we offer a timely resolution to your cleaning and maintenance needs.</p>
</div>
<div class="abs btn about-btn">READ MORE</div>

<section class="abs why" role="img" aria-label="Dark workshop backdrop with a perforated metal sheet"></section>
<h2 class="abs section-title display why-title">WHY CHOOSE LASER</h2>
<div class="abs why-card" style="left:111px;width:173px">
  <svg width="68" height="68" viewBox="0 0 68 68" fill="none" stroke="var(--icon-blue)" stroke-width="4"><circle cx="34" cy="34" r="10" fill="var(--icon-blue)"/><path d="M8 8l14 14M22 12v10H12M60 8L46 22M46 12v10h10M8 60l14-14M12 46h10v10M60 60L46 46M56 46H46v10"/></svg>
  Minimum<br>Downtime
</div>
<div class="abs why-card active" style="left:284px;width:237px">
  <svg width="72" height="72" viewBox="0 0 72 72" fill="none" stroke="#fff" stroke-width="4"><path d="M36 4v16M28 12l8-8 8 8"/><path d="M12 30l24-10 24 10v26L36 68 12 56z"/><path d="M12 30l24 12 24-12M36 42v26"/></svg>
  No surface<br>Damage
</div>
<div class="abs why-card" style="left:521px;width:172px">
  <svg width="72" height="68" viewBox="0 0 72 68" fill="var(--icon-blue)"><path d="M40 34c0-14 8-22 22-24-2 14-10 22-22 24z"/><path d="M38 34c0-10-6-16-16-18 1 10 7 16 16 18z"/><rect x="37" y="30" width="3" height="14"/><path d="M4 50h14l10 4h14c4 0 4 6 0 6H28v2h16l20-10c4-2 6 3 2 5L44 68H4z"/></svg>
  No Environmental<br>Impact
</div>
<div class="abs why-card" style="left:704px;width:186px">
  <svg width="72" height="72" viewBox="0 0 72 72" fill="none" stroke="var(--icon-blue)" stroke-width="4"><path d="M12 4v64M28 4v64M44 4v64M60 4v64M4 22h64M4 50h64"/></svg>
  No Mess
</div>
<div class="abs why-card" style="left:902px;width:186px">
  <svg width="60" height="72" viewBox="0 0 60 72" fill="var(--icon-blue)"><rect x="4" y="10" width="52" height="6"/><rect x="22" y="2" width="16" height="6"/><path d="M8 20h44l-4 50H12z"/><rect x="18" y="28" width="4" height="34" fill="#fff"/><rect x="28" y="28" width="4" height="34" fill="#fff"/><rect x="38" y="28" width="4" height="34" fill="#fff"/></svg>
  No Waste
</div>

<div class="abs video" role="img" aria-label="Explainer video still: laser cutting perforated steel with sparks">
  <div class="abs play"><svg width="22" height="24" viewBox="0 0 22 24"><path d="M3 2l17 10L3 22z" fill="#fff"/></svg></div>
</div>

<div class="abs tabs">
  <div class="tab">CONTAMINANTS</div>
  <div class="tab active">SURFACES</div>
  <div class="tab">INDUSTRIES</div>
</div>

<div class="abs surface" style="left:138px;top:2874px"><div class="disc"><svg width="48" height="48" viewBox="0 0 48 48" fill="#fff"><path d="M6 34l18-22h18L24 34z"/><path d="M6 38h18v4H6zM26 36l16-20v8L26 42z"/></svg></div>Metals</div>
<div class="abs surface" style="left:333px;top:2874px"><div class="disc"><svg width="52" height="44" viewBox="0 0 52 44" fill="#fff"><rect x="12" y="10" width="30" height="26" rx="3"/><rect x="4" y="18" width="8" height="10"/><rect x="42" y="16" width="6" height="14"/><rect x="18" y="4" width="16" height="6"/><path d="M28 14l-6 10h5l-3 8 8-11h-5l3-7z" fill="#1d1d1d"/></svg></div>Engines</div>
<div class="abs surface" style="left:529px;top:2874px"><div class="disc"><svg width="46" height="46" viewBox="0 0 46 46" fill="none" stroke="#fff" stroke-width="5"><circle cx="23" cy="23" r="14"/><path d="M23 23l-14 14" stroke-linecap="round"/><circle cx="23" cy="23" r="4" fill="#fff"/></svg></div>Tools</div>
<div class="abs surface" style="left:725px;top:2874px"><div class="disc"><svg width="48" height="48" viewBox="0 0 48 48" fill="#fff"><rect x="8" y="4" width="16" height="16"/><rect x="4" y="24" width="40" height="14" rx="7"/><circle cx="14" cy="31" r="4" fill="#1d1d1d"/><circle cx="34" cy="31" r="4" fill="#1d1d1d"/><rect x="4" y="40" width="40" height="4"/></svg></div>Machinery</div>
<div class="abs surface" style="left:921px;top:2874px"><div class="disc"><svg width="50" height="44" viewBox="0 0 50 44" fill="#fff"><rect x="17" y="2" width="16" height="10"/><rect x="7" y="16" width="16" height="10"/><rect x="27" y="16" width="16" height="10"/><rect x="0" y="30" width="16" height="10"/><rect x="18" y="30" width="14" height="10"/><rect x="34" y="30" width="16" height="10"/></svg></div>Bricks</div>

<div class="abs surface" style="left:138px;top:3063px"><div class="disc"><svg width="54" height="42" viewBox="0 0 54 42" fill="#fff"><path d="M2 12h18v20H2z"/><path d="M22 6l22 4v18H22z"/><rect x="2" y="30" width="50" height="4"/><circle cx="12" cy="36" r="5"/><circle cx="40" cy="36" r="5"/></svg></div>Concrete</div>
<div class="abs surface" style="left:333px;top:3063px"><div class="disc"><svg width="50" height="48" viewBox="0 0 50 48" fill="#fff"><path d="M24 4C10 4 2 14 2 24s8 20 20 20c6 0 6-6 2-8s-2-8 4-8h8c6 0 10-4 10-10C46 10 36 4 24 4z"/><circle cx="14" cy="18" r="4" fill="#1d1d1d"/><circle cx="26" cy="12" r="4" fill="#1d1d1d"/><circle cx="12" cy="30" r="4" fill="#1d1d1d"/><path d="M48 10L30 32l-4-2 18-24z"/></svg></div>Paint</div>
<div class="abs surface" style="left:529px;top:3063px"><div class="disc"><svg width="48" height="48" viewBox="0 0 48 48" fill="none" stroke="#fff" stroke-width="4"><rect x="4" y="4" width="40" height="40"/><path d="M4 20l14-4 6 10 20-6M18 16l4-12M24 26l-6 18M24 26l20 8"/></svg></div>Stone</div>
<div class="abs surface" style="left:725px;top:3063px"><div class="disc"><svg width="52" height="44" viewBox="0 0 52 44" fill="#fff"><rect x="16" y="4" width="30" height="16" rx="8"/><rect x="16" y="24" width="30" height="16" rx="8"/><circle cx="12" cy="12" r="8" stroke="#1d1d1d" stroke-width="2"/><circle cx="12" cy="32" r="8" stroke="#1d1d1d" stroke-width="2"/></svg></div>Wood</div>
<div class="abs surface" style="left:921px;top:3063px"><div class="disc"><svg width="44" height="50" viewBox="0 0 44 50" fill="none" stroke="#fff" stroke-width="4"><rect x="4" y="4" width="36" height="42"/><path d="M14 12l-4 26M24 10l-6 32M34 12l-4 24"/></svg></div>Aluminium</div>

<footer class="abs site-footer" role="img" aria-label="Dark industrial backdrop with faint sparks"></footer>
<div class="abs foot-col" style="left:110px">
  <h3>LINKS</h3>
  <ul><li>»<span>Home</span></li><li>»<span>About</span></li><li>»<span>Testimonials</span></li><li>»<span>Contact</span></li></ul>
</div>
<div class="abs foot-col" style="left:354px">
  <h3>INFORMATION</h3>
  <ul><li>»<span>About</span></li><li>»<span>Services</span></li><li>»<span>Privacy Policy</span></li><li>»<span>Terms of Condition</span></li></ul>
</div>
<div class="abs foot-col" style="left:650px">
  <h3>SUPPORT</h3>
  <ul>
    <li><svg width="11" height="14" viewBox="0 0 12 16"><path fill="#fff" d="M6 0a6 6 0 0 0-6 6c0 4.5 6 10 6 10s6-5.5 6-10a6 6 0 0 0-6-6zm0 8.5A2.5 2.5 0 1 1 6 3.5a2.5 2.5 0 0 1 0 5z"/></svg><span>Lorem ipsum dolor sit amet</span></li>
    <li><svg width="12" height="12" viewBox="0 0 24 24"><path fill="#fff" d="M6.6 10.8a15 15 0 0 0 6.6 6.6l2.2-2.2c.3-.3.7-.4 1-.2 1.1.4 2.3.6 3.6.6.6 0 1 .4 1 1V20c0 .6-.4 1-1 1A17 17 0 0 1 3 4c0-.6.4-1 1-1h3.5c.6 0 1 .4 1 1 0 1.3.2 2.5.6 3.6.1.3 0 .7-.2 1z"/></svg><span>+61 3 9555 0142</span></li>
    <li><svg width="13" height="10" viewBox="0 0 14 10"><rect width="14" height="10" fill="#fff"/><path d="M0 0l7 5 7-5" fill="none" stroke="#141820"/></svg><span>hello@brightformbeam.com.au</span></li>
  </ul>
</div>
<div class="abs foot-col" style="left:947px">
  <h3>FOLLOW US</h3>
  <div class="social" aria-label="Social links"><span></span><span></span><span></span><span></span></div>
</div>
<p class="abs copyright">© Copyrights Brightform Beam Services 2023. All rights reserved</p>

</body>
</html>
```